Velvet Lantern rebranding my business with a new business card

I have my new logo and now I need a refresher on my business cards. I really want something fun and fresh. I like black background or anything to make the color pop.
Logo
Name: Velvet Lantern
Contact Info as stated below:
Mira Pellow
555-013-4762
Logo
Name: Velvet Lantern
Mira Pellow
555-013-4762
fb.me/VelvetLanternbyMira
Instagram: @VelvetLanternbyMira

Industry/Entity Type

Business

Contact Information for Business Card

double-sided. Logo on one side. Contact info on the other.

Requirements
Must have
• Logo
• Name: Velvet Lantern
• Contact Info as stated below:
• Mira Pellow
• 555-013-4762
• fb.me/VelvetLanternbyMira
• fb.me/VelvetLanternbyMira

```html
<!DOCTYPE html>
<html lang="en">
<head>
<meta charset="utf-8">
<title>Velvet Lantern – Business Card</title>
<link href="https://fonts.googleapis.com/css2?family=Mulish:wght@400;600&display=swap" rel="stylesheet">
<style>
  :root {
    --page: #1b1b1d;
    --teal: #33b8a0;
    --white: #ffffff;
    --tan: #cfc3a0;
    --red: #b3222a;
    --pink: #e9a9bd;
    --ink-light: #ffffff;
    --logo-ink: #4a3a34;
  }
  * { box-sizing: border-box; margin: 0; padding: 0; }
  html, body { width: 1200px; height: 963px; overflow: hidden; }
  body {
    background: var(--page);
    font-family: "Mulish", sans-serif;
    position: relative;
  }
  .card {
    position: absolute;
    left: 250px;
    width: 700px;
    height: 400px;
    border-radius: 18px;
    overflow: hidden;
  }
  .card--front { top: 60px; background: var(--white); }
  .card--back { top: 503px; background: var(--teal); }
  .card-art { position: absolute; left: 0; top: 0; width: 700px; height: 400px; }

  .brand-name {
    font-family: "Mulish", sans-serif;
    font-weight: 600;
    color: var(--logo-ink);
    text-align: center;
    letter-spacing: 1px;
  }
  .front-logo {
    position: absolute;
    left: 125px; top: 25px;
    width: 210px; height: 210px;
    display: flex; align-items: center; justify-content: center;
    font-size: 22px;
  }
  .social {
    position: absolute;
    left: 34px; top: 270px;
    color: var(--ink-light);
    font-size: 15px;
    display: flex; align-items: center; gap: 7px;
  }
  .social .mark { width: 11px; height: 11px; background: var(--ink-light); border-radius: 2px; flex-shrink: 0; }
  .contact {
    position: absolute;
    right: 80px; bottom: 26px;
    color: var(--ink-light);
    text-align: right;
  }
  .contact .person { font-size: 22px; letter-spacing: 2px; text-transform: uppercase; line-height: 1.25; }
  .contact .role { font-size: 15px; margin-bottom: 8px; line-height: 1.25; }
  .contact .line { font-size: 16px; display: flex; justify-content: flex-end; align-items: center; gap: 10px; line-height: 1.45; }
  .contact .line svg { width: 14px; height: 14px; flex-shrink: 0; }

  .back-logo {
    position: absolute;
    left: 0; right: 0; top: 160px;
    font-size: 30px;
  }
</style>
</head>
<body>

<section class="card card--front">
  <svg class="card-art" viewBox="0 0 700 400" aria-hidden="true">
    <path d="M0,100 C40,160 110,220 230,245 L0,245 Z" fill="var(--red)"/>
    <path d="M0,125 C50,185 120,228 240,242 L0,242 Z" fill="var(--white)"/>
    <path d="M0,210 C150,270 360,230 500,240 C590,246 660,285 700,300 L700,400 L0,400 Z" fill="var(--teal)"/>
    <path d="M0,203 C150,263 360,223 500,233 C592,239 662,278 706,293" fill="none" stroke="var(--tan)" stroke-width="7"/>
    <circle cx="230" cy="130" r="105" fill="var(--white)" stroke="#222" stroke-width="2"/>
    <circle cx="230" cy="130" r="96" fill="none" stroke="var(--pink)" stroke-width="2"/>
    <circle cx="230" cy="130" r="91" fill="none" stroke="var(--pink)" stroke-width="1"/>
  </svg>
  <div class="brand-name front-logo">Velvet Lantern</div>
  <div class="social"><span class="mark"></span>fb.me/VelvetLanternbyMira</div>
  <div class="contact">
    <div class="person">Mira Pellow</div>
    <div class="role">Owner</div>
    <div class="line">555-013-4762
      <svg viewBox="0 0 14 14"><rect x="3.5" y="1" width="7" height="12" rx="1.5" fill="none" stroke="currentColor" stroke-width="1.4"/></svg>
    </div>
    <div class="line">info@velvetlanternbakes.com
      <svg viewBox="0 0 14 14"><rect x="1" y="3" width="12" height="8" fill="currentColor"/><path d="M1,3 L7,8 L13,3" fill="none" stroke="var(--teal)" stroke-width="1.2"/></svg>
    </div>
  </div>
</section>

<section class="card card--back">
  <div class="brand-name back-logo">Velvet Lantern</div>
</section>

</body>
</html>
```